Wordpress Business Travel Blog and Discussion Board

Oh, Hello!

We are looking for a motivated designer to create a full, turnkey interactive WordPress website geared toward business travel that includes a news style blog (look at ByteHarbor.com and Wirevane.com for the style we like) that is seamlessly integrated with a robust message board (look at GateBanter.com and RoamLedger.com). Ok, so stick with us here because this is actually a pretty cool project that shouldn't be too hard, but yes, of course we have some curve balls that we are throwing your way. Sorry! :)

*On the front page*

- We would like to have a typical news style blog layout that is fun, somewhat professional, and easy to read. That's easy!

- Somewhere within first glance, we would like to have a short list of the most active discussions on our discussion board. (What's trending, or something like that). Not too bad, right?

- Overall, want to have a good amount of content, but we also do not want the visitor to feel as if he or she is having to sift through a lot of content to see what he or she wants to see. Great! We're past the beginning!

We will have traditional visual advertising on all of our pages. Please leave space as necessary :)

*On the Blog/News story pages*

Let's keep these simple - but there is a twist!

Let's say I create a blog/news post. I would like that blog/news post to also be opened as a discussion on the discussion board. For example, I write an article about Coastal Skyways and their service on a particular international flight. This will be opened as a discussion under the Coastal Skyways topic in the discussion board. Other users can also open new discussions under any topic on the discussion board, but they cannot post stories (unless permission is given) to the blog wall. We would like their posts to show up as regular discussion board posts while the news/blog posts by us show up as news/blog posts on the front page, *and* (oh yes we did!) as discussions in the discussion board. Of course, users will still be able to post comments to the news/blog post, which will also be posted in the discussion.

OK, does that make sense? Let me know if I can help make this more clear! :) Sorry!

*Wiki Pages*

Take a look at the Coastal Skyways example above. In that example, my news/blog entry automatically opens a new discussion post. Although we won't necessarily need to create a new wiki page, we would like to tag the post and the discussion to a wiki page about the topic. The wiki page can be created and edited by all users (and locked by us if necessary). BONUS! Can we tag more than one wiki page?

*Websites that inspire us*

ByteHarbor.com - concept and design
Wirevane.com - concept and design
GateBanter.com - concept
RoamLedger.com - concept
pomwhispers.com - concept

All of the sites above are great and we can only thrive with their great success. We are not aiming to be a competitor to the travel sites, but just another great option for interested visitors. Please do not simply copy what they have. What is posted above is a list of our favorite sites that we visit every day.

Our favorite font is Segoe UI, but please don't use this (or a similar font) too much! Maybe just titles would be great. You're the designer so you can make the call here.

Also, our favorite color is blue, but if you have another favorite color, go ahead and show us what you can do! (Don't use too much blue!)

*Oh, and One More Thing*

(I know, you thought we were done. We're not!)

Here's the killer - We would like to create a way for people to, say, enter the details of their next trip and be matched with someone who will also be on a portion of their trip.

For example, let's say I am flying Meridian Airways flight 109 from Los Angeles to New York JFK Airport this Friday. I am staying at the Bellcourt New York Times Square on Friday night, and I am flying back on Saturday night on Kestrel flight 290 from New York JFK airport back to Los Angeles. Another user will also be on the Kestrel flight back to Los Angeles with me and he entered that information in the website. (Note, the user has to manually enter this information). The other user and I will both be notified that there is at least one other user who will be on the same Kestrel flight as me. We will both have the option to reveal our online identity - which will in fact be released to each person as long as each person *mutually* agrees.

This can be very simple - almost like a dating site type of match but it is based on two people being in the same place at the same time (based on what they report). Also, we would like to be able to collect this information - not necessarily tied to the user's true identity. The information we would like to have is - what the user is claiming he or she is doing on the trip (i.e. staying at the Bellcourt Times Square, flying Meridian Airways), and whether or not the user agreed to reveal his or her identity - AND! whether or not the users both revealed their identity.

*Most Important*

HAVE FUN and THANK YOU!! :)

A couple of quick notes - this is a design and code project. We are most likely offering a more $(!) design and code project for the version 2.0 of this website once we get user feedback from this first round.

Also, the name of the website is Jaunta. (www.jaunta-example.com)

Good luck!

Reason: Extending as requested by a few designers. Only 3 more days to get your designs in!

Reason: All designs look great! Last chance for one or two more designers who have requested an extension. All designs that were already submitted on time will be considered with much higher priority. Thank you!

Requirements
Must have
• We need to have a high end, professional, modern, and clean design on the front page to entice readers to constantly visit and stay on our site.
Nice to have
• It would be great to give us the ability to automatically recognize users for visiting the website and/or participating and commenting. Social badges, recognition, etc. would be very cool.
Should not have
• Although this is a website around business travel, we do not necessarily want it to be business travel themed. There can be hints of the theme, but otherwise the visual look should be somewhat generic.

```html
<!DOCTYPE html>
<html lang="en">
<head>
<meta charset="utf-8">
<title>Jaunta — Business Travel Blog</title>
<link rel="stylesheet" href="https://fonts.googleapis.com/css2?family=Open+Sans:wght@400;600;700&family=Arimo:wght@400;700&display=swap">
<style>
:root{
  --page-bg:#0c1822;
  --stripe:#112230;
  --blue:#1a7fc1;
  --blue-dark:#0f5e96;
  --blue-band:#1874b4;
  --footer-dark:#0d3d63;
  --ink:#1c1c1c;
  --muted:#6a6a6a;
  --rule:#d9d9d9;
  --panel:#ffffff;
  --soft:#f0f0f0;
  --orange:#f7941d;
  --green:#6ab42d;
  --title-font:"Open Sans",sans-serif;
  --body-font:"Arimo",sans-serif;
}
*{box-sizing:border-box;margin:0;padding:0}
html,body{width:697px;height:1200px;overflow:hidden}
body{
  position:relative;font-family:var(--body-font);color:var(--ink);
  background:repeating-linear-gradient(90deg,var(--page-bg) 0 3px,var(--stripe) 3px 5px);
}
.abs{position:absolute}
a{color:inherit;text-decoration:none}

/* top utility nav */
.top-nav{left:259px;top:2px;display:flex;gap:10px;font:700 7.5px/10px var(--body-font);color:#fff}

/* header */
.brand-band{left:85px;top:15px;width:350px;height:42px;
  background:linear-gradient(180deg,#6cb6e6 0%,#a9d8f3 55%,#dff1fb 100%)}
.brand-band .sky{position:absolute;left:170px;top:0;width:180px;height:42px;
  background:linear-gradient(100deg,rgba(255,255,255,0) 0%,rgba(255,255,255,.55) 60%,rgba(190,220,240,.6) 100%)}
.logo{position:absolute;left:9px;top:7px;font:700 21px/26px var(--title-font);color:#fff}
.search{left:446px;top:28px;width:163px;height:14px;background:#fff;border-radius:8px;
  font:400 7px/14px var(--body-font);color:#777;padding-left:8px}
.search .go{position:absolute;right:0;top:0;width:16px;height:14px;border-radius:0 8px 8px 0;background:var(--green)}
.search .go svg{position:absolute;left:4px;top:3px}

.main-nav{left:0;top:57px;width:697px;height:13px;background:linear-gradient(#fafafa,#d8d8d8)}
.main-nav ul{position:absolute;left:91px;top:0;display:flex;gap:14px;list-style:none;font:400 7.5px/13px var(--body-font);color:var(--blue-dark)}
.account{position:absolute;left:505px;top:0;width:104px;height:13px;background:var(--blue);
  font:400 7px/13px var(--body-font);color:#fff;display:flex;gap:8px;padding-left:10px;border-radius:4px 0 0 0}

/* main column */
.main{left:85px;top:70px;width:350px;height:1077px;background:var(--panel)}
.feature-title{left:5px;top:5px;width:170px;font:700 12.5px/14px var(--title-font);color:#333}
.video{left:5px;top:37px;width:173px;height:121px;
  background:linear-gradient(135deg,#e8e0d6 0%,#c9a58a 40%,#8b5a4a 70%,#d9d2c9 100%)}
.controls{left:5px;top:158px;width:173px;height:12px;background:linear-gradient(#f4f4f4,#cfcfcf);
  font:400 6.5px/12px var(--body-font);color:#333}
.highlights{left:185px;top:4px;width:160px}
.section-label{font:700 10px/14px var(--title-font);color:var(--blue);border-bottom:1px solid var(--blue-dark);padding-bottom:2px}
.hl-item{display:flex;gap:8px;background:var(--soft);border-radius:3px;height:44px;padding:4px 5px;margin-top:7px}
.thumb{flex:none;background:linear-gradient(160deg,#cfe0ee,#7f9db8 60%,#3c4f63)}
.hl-item .thumb{width:47px;height:36px}
.hl-item p{width:88px;font:400 7.5px/10px var(--body-font);color:#333}
.view-all{right:6px;top:182px;font:700 9px/12px var(--title-font);color:var(--blue)}
.rule{left:5px;width:340px;height:1px;background:var(--rule)}

.post{left:5px;width:340px}
.share-col{position:absolute;left:0;top:0;width:56px}
.bubble{width:30px;height:13px;border-radius:7px;background:#8bb4d8;color:#fff;
  font:700 7px/13px var(--body-font);text-align:center;margin:2px 0 5px 2px;position:relative}
.bubble::after{content:"";position:absolute;left:6px;bottom:-3px;border:3px solid transparent;border-top-color:#8bb4d8;border-bottom:0}
.sbtn{display:flex;align-items:center;gap:3px;height:11px;margin-bottom:4px;font:700 6px/11px var(--body-font);color:#333}
.sbtn b{display:flex;gap:2px;align-items:center;border:1px solid #c8c8c8;border-radius:2px;padding:0 2px;background:#f6f6f6;height:10px;line-height:9px}
.sbtn i{width:6px;height:6px;display:inline-block}
.sbtn .n{font-weight:400;border:1px solid #ccc;padding:0 2px;height:9px;line-height:8px;background:#fff}
.byline{position:absolute;left:66px;top:4px;font:400 6px/8px var(--body-font);color:#555}
.byline span{display:block;color:var(--blue);text-transform:uppercase}
.post h2{position:absolute;left:66px;width:245px;font:700 16px/16.5px var(--title-font);color:#111}
.post-img{position:absolute;left:66px}
.text{position:absolute;font:400 7px/11.6px var(--body-font);color:var(--muted)}
.more{color:var(--blue);font-weight:700}
.caption{position:absolute;left:0;bottom:0;width:100%;height:36px;background:rgba(40,40,40,.75);
  font:400 7px/36px var(--body-font);color:#fff;padding-left:30px}
.caption svg{position:absolute;left:10px;top:13px}
.next{left:5px;top:1052px;width:340px;height:19px;background:var(--blue);
  font:700 13px/19px var(--title-font);color:#fff;text-align:right;padding-right:14px}

/* sidebar */
.box{left:441px;width:168px;background:var(--panel);border-top:3px solid #dcdcdc}
.box h3{font:700 8.5px/12px var(--title-font);color:var(--blue);padding:4px 6px 3px;border-bottom:1px solid #e4e4e4}
.ad{left:441px;top:74px;width:168px;height:143px;background:#fff;padding:4px 3px}
.ad-slot{width:162px;height:135px;background:linear-gradient(160deg,#f9ad45,var(--orange) 60%,#e9801a)}
.field{display:flex;align-items:center;margin:7px 0 0 6px;font:400 7px/12px var(--body-font);color:#444}
.field label{width:58px}
.field .in{width:72px;height:12px;border:1px solid #ccc}
.field .ic{margin-left:8px;width:12px;height:11px;background:#5ab0e6;border-radius:2px}
.btn{background:var(--blue-dark);color:#fff;font:400 7px/12px var(--body-font);text-align:center}
.tabs{display:flex;height:26px;border-bottom:1px solid #ddd;background:#f3f3f3}
.tabs div{flex:1;font:400 8px/9px var(--title-font);color:#999;padding:4px 0 0 11px;border-right:1px solid #ddd}
.tabs .on{background:#fff;color:var(--blue)}
.trend{display:flex;gap:8px;height:55px;padding:10px 0 0 10px;border-bottom:1px solid #eee}
.trend .thumb{width:52px;height:38px}
.trend p{width:84px;font:400 8.5px/9px var(--body-font);color:#222}
.sub{display:flex;margin:11px 6px 0}
.sub .in{width:118px;height:15px;border:1px solid #ccc;font:400 7px/13px var(--body-font);color:#333;padding-left:5px}
.sub .btn{width:35px;height:15px;line-height:15px;margin-left:3px;border-radius:2px;background:var(--blue)}
.soc-row{display:flex;gap:6px;align-items:center;padding:14px 12px;border-bottom:1px solid #eee;font:400 5.5px/7px var(--body-font);color:#555}
.pill{border:1px solid #bbb;border-radius:2px;background:#f3f3f3;font:700 6.5px/14px var(--body-font);color:#333;padding:0 4px;white-space:nowrap;display:flex;gap:3px;align-items:center}
.icons{display:flex;gap:5px;padding:13px 11px}
.icons span{width:25px;height:25px;border-radius:4px}

/* footer */
.foot-top{left:85px;top:1147px;width:530px;height:14px;background:var(--blue-band)}
.foot-top ul{display:flex;gap:24px;list-style:none;font:400 7.5px/14px var(--body-font);color:#fff;padding-left:13px}
.foot-top .dots{position:absolute;right:8px;top:3px;display:flex;gap:4px}
.foot-top .dots span{width:8px;height:8px;background:#fff;border-radius:1px}
.foot-bottom{left:85px;top:1161px;width:530px;height:30px;background:var(--footer-dark)}
.foot-logo{position:absolute;left:12px;top:2px;font:700 17px/24px var(--title-font);color:#c7dbe9}
.legal{position:absolute;right:9px;top:8px;font:400 7px/10px var(--body-font);color:#a9c6dc;word-spacing:1px}
</style>
</head>
<body>

<nav class="abs top-nav"><a>Home</a><a>Blog</a><a>Forums</a><a>Members</a><a>Wiki</a><a>Help</a></nav>

<header class="abs brand-band">
  <div class="sky" role="img" aria-label="Airliner flying over a bright sky"></div>
  <div class="logo">Jaunta</div>
</header>
<div class="abs search">Search<span class="go"><svg width="8" height="8" viewBox="0 0 8 8"><circle cx="3.2" cy="3.2" r="2.3" fill="none" stroke="#fff" stroke-width="1.2"/><path d="M5 5l2.3 2.3" stroke="#fff" stroke-width="1.2"/></svg></span></div>

<div class="abs main-nav">
  <ul><li>Miles &amp; Points</li><li>Travel &amp; Dining</li><li>Community</li><li>OMNI</li><li>Destinations</li></ul>
  <div class="account"><span>Register Now</span><span>Login</span></div>
</div>

<main class="abs main">
  <h1 class="abs feature-title">Nullam ac lectus nisi, id commodo sem.</h1>
  <div class="abs video" role="img" aria-label="Smiling family boarding an airplane"></div>
  <div class="abs controls">
    <svg width="173" height="12" viewBox="0 0 173 12">
      <path d="M6 3l5 3-5 3z" fill="#222"/>
      <path d="M18 4.5h2l3-2v7l-3-2h-2z" fill="#222"/>
      <rect x="40" y="5" width="28" height="2" fill="#1a7fc1"/>
      <rect x="68" y="5" width="14" height="2" fill="#999"/>
      <circle cx="68" cy="6" r="2.5" fill="#fff" stroke="#888" stroke-width=".6"/>
      <path d="M148 3.5a2.5 2.5 0 1 0 2 1" fill="none" stroke="#222" stroke-width="1"/>
      <rect x="160" y="3" width="8" height="6" fill="#222"/>
    </svg>
    <span style="position:absolute;left:88px;top:0">42:15</span>
    <span style="position:absolute;left:118px;top:0">Share</span>
  </div>

  <section class="abs highlights">
    <h2 class="section-label">HIGHLIGHTS</h2>
    <div class="hl-item"><div class="thumb" role="img" aria-label="Airport terminal interior"></div><p>Lorem ipsum dolor sit amet, consectetur adipiscing elit.</p></div>
    <div class="hl-item"><div class="thumb" role="img" aria-label="Traveller at a departure gate"></div><p>Maecenas sit amet massa metus, id semper diam.</p></div>
    <div class="hl-item"><div class="thumb" role="img" aria-label="Business traveller with luggage"></div><p>Donec feugiat ligula non odio ullamcorper nec luctus turpis vehicula.</p></div>
  </section>
  <a class="abs view-all">View all videos ▸</a>
  <div class="abs rule" style="top:200px"></div>

  <article class="abs post" style="top:213px;height:275px">
    <div class="share-col">
      <div class="bubble">18</div>
      <div class="sbtn"><b><i style="background:#3b5998"></i>Like</b><span class="n">251</span></div>
      <div class="sbtn"><b><i style="background:#55acee"></i>Tweet</b><span class="n">483</span></div>
      <div class="sbtn"><b><i style="background:#0e76a8"></i>Share</b><span class="n">21</span></div>
      <div class="sbtn"><b><i style="background:#d34836"></i>+1</b><span class="n">17</span></div>
    </div>
    <div class="byline"><span>Dana Whitford</span>posted 51 mins ago</div>
    <h2 style="top:21px">Fusce commodo ligula consequat lacus venenatis congue condimentum neque auctor.</h2>
    <div class="post-img" style="top:96px;width:116px;height:92px;background:linear-gradient(170deg,#5d6f86,#b59a86 55%,#3c3f48)" role="img" aria-label="Passenger jet landing at sunset"></div>
    <p class="text" style="left:193px;top:95px;width:147px">Sed ut perspiciatis unde omnis iste natus error sit voluptatem accusantium doloremque laudantium, totam rem aperiam, eaque ipsa quae ab illo inventore veritatis et quasi architecto beatae vitae dicta sunt explicabo. Nemo enim ipsam voluptatem quia voluptas sit aspernatur aut odit aut fugit, sed quia consequuntur magni dolores eos qui</p>
    <p class="text" style="left:66px;top:197px;width:274px">Sed ut perspiciatis unde omnis iste natus error sit voluptatem accusantium doloremque laudantium, totam rem aperiam, eaque ipsa quae ab illo inventore veritatis et quasi architecto beatae vitae dicta sunt explicabo. Nemo enim ipsam voluptatem quia voluptas sit aspernatur aut odit aut fugit, sed quia consequuntur magni dolores eos qui ratione voluptatem sequi nesciunt. Neque porro quisquam est, qui dolorem <a class="more">⟶Read More</a></p>
  </article>
  <div class="abs rule" style="top:488px"></div>

  <article class="abs post" style="top:505px;height:200px">
    <div class="share-col">
      <div class="bubble">6</div>
      <div class="sbtn"><b><i style="background:#3b5998"></i>Like</b><span class="n">251</span></div>
      <div class="sbtn"><b><i style="background:#55acee"></i>Tweet</b><span class="n">483</span></div>
      <div class="sbtn"><b><i style="background:#0e76a8"></i>Share</b><span class="n">21</span></div>
      <div class="sbtn"><b><i style="background:#d34836"></i>+1</b><span class="n">17</span></div>
    </div>
    <div class="byline"><span>Rosa Quintero</span>posted yesterday</div>
    <h2 style="top:21px">Donec volutpat dapibus lacus, in convallis magna aliquam in.</h2>
    <div class="post-img" style="top:68px;width:116px;height:92px;background:linear-gradient(160deg,#c9dbe8,#8aa5bb 50%,#4a5666)" role="img" aria-label="Travellers walking through an airport concourse"></div>
    <p class="text" style="left:193px;top:67px;width:147px">Sed ut perspiciatis unde omnis iste natus error sit voluptatem accusantium doloremque laudantium, totam rem aperiam, eaque ipsa quae ab illo inventore veritatis et quasi architecto beatae vitae dicta sunt explicabo. Nemo enim ipsam voluptatem quia voluptas sit aspernatur aut odit aut fugit, sed quia consequuntur magni dolores eos qui ratione voluptatem sequi nesciunt. Neque porro quisquam <a class="more">⟶Read More</a></p>
  </article>
  <div class="abs rule" style="top:705px"></div>

  <article class="abs post" style="top:722px;height:325px">
    <div class="share-col">
      <div class="bubble">6</div>
      <div class="sbtn"><b><i style="background:#3b5998"></i>Like</b><span class="n">251</span></div>
      <div class="sbtn"><b><i style="background:#55acee"></i>Tweet</b><span class="n">483</span></div>
      <div class="sbtn"><b><i style="background:#0e76a8"></i>Share</b><span class="n">21</span></div>
      <div class="sbtn"><b><i style="background:#d34836"></i>+1</b><span class="n">17</span></div>
    </div>
    <div class="byline"><span>Rosa Quintero</span>posted yesterday</div>
    <h2 style="top:21px">Phasellus consectetur erat nec tortor lobortis sed vestibulum massa tristique.</h2>
    <div class="post-img" style="top:78px;width:269px;height:164px;background:linear-gradient(170deg,#e6e6e2,#b9b7b0 45%,#5a5e66)" role="img" aria-label="Two business travellers waiting at an airport gate">
      <div class="caption"><svg width="10" height="10" viewBox="0 0 10 10"><path d="M1 0l9 5-9 5z" fill="#fff"/></svg>Sed ut perspiciatis unde omnis</div>
    </div>
    <p class="text" style="left:66px;top:250px;width:274px">Sed ut perspiciatis unde omnis iste natus error sit voluptatem accusantium doloremque laudantium, totam rem aperiam, eaque ipsa quae ab illo inventore veritatis et quasi architecto beatae vitae dicta sunt explicabo. Nemo enim ipsam voluptatem quia voluptas sit aspernatur aut odit aut fugit, sed quia consequuntur magni dolores eos qui ratione voluptatem sequi nesciunt. Neque porro quisquam <a class="more">⟶Read More</a></p>
  </article>

  <a class="abs next">Next ▸</a>
</main>

<aside>
  <div class="abs ad">
    <div class="ad-slot" role="img" aria-label="Advertising banner space"></div>
  </div>

  <section class="abs box" style="top:221px;height:85px">
    <h3>MATCH A PORTION ON YOUR TRIP!</h3>
    <div class="field"><label>Start Date</label><span class="in"></span><span class="ic"></span></div>
    <div class="field"><label>Flight Number</label><span class="in"></span><span class="ic" style="background:#c9c9c9"></span></div>
    <div class="btn" style="position:absolute;left:64px;top:66px;width:36px;height:12px">Search</div>
  </section>

  <section class="abs box" style="top:311px;height:308px;border-top-width:1px">
    <div class="tabs"><div class="on">Recent<br>Trending</div><div>Archieve<br>Trending</div><div>All<br>Trending</div></div>
    <div class="trend"><div class="thumb" role="img" aria-label="Traveller in an airport"></div><p>Maecenas sit amet massa metus, id semper diam.</p></div>
    <div class="trend"><div class="thumb" role="img" aria-label="Traveller in an airport"></div><p>Maecenas sit amet massa metus, id semper diam.</p></div>
    <div class="trend"><div class="thumb" role="img" aria-label="Traveller in an airport"></div><p>Maecenas sit amet massa metus, id semper diam.</p></div>
    <div class="trend"><div class="thumb" role="img" aria-label="Traveller in an airport"></div><p>Maecenas sit amet massa metus, id semper diam.</p></div>
    <div class="trend" style="border:0"><div class="thumb" role="img" aria-label="Traveller in an airport"></div><p>Maecenas sit amet massa metus, id semper diam.</p></div>
  </section>

  <section class="abs box" style="top:623px;height:57px">
    <h3>NEWSLETTERS</h3>
    <div class="sub"><span class="in">Enter your e-mail address</span><span class="btn">Subscribe</span></div>
  </section>

  <section class="abs box" style="top:686px;height:156px">
    <h3>SOCIALIZE</h3>
    <div class="soc-row"><span class="pill"><i style="width:6px;height:6px;background:#3b5998;display:inline-block"></i>Like</span><span>498,909 people like this. Sign Up to see what your friends like.</span></div>
    <div class="soc-row" style="gap:5px;padding-left:14px"><span class="pill"><i style="width:6px;height:6px;background:#55acee;display:inline-block"></i>Follow @Jaunta</span><span class="pill" style="font-weight:400">2.3M followers</span></div>
    <div class="icons">
      <span style="background:#3b5998"></span><span style="background:#3fa9d8"></span><span style="background:#1c6fa3"></span><span style="background:#c9302c"></span><span style="background:#ee7a22"></span>
    </div>
  </section>
</aside>

<footer>
  <div class="abs foot-top">
    <ul><li>Home</li><li>Blog</li><li>Forums</li><li>Members</li><li>Wiki</li><li>Help</li></ul>
    <div class="dots"><span></span><span></span></div>
  </div>
  <div class="abs foot-bottom">
    <div class="foot-logo">Jaunta</div>
    <div class="legal">Privacy Policy &nbsp; | &nbsp; Terms Of Service &nbsp; | &nbsp; © 2012 Jaunta. All rights reserved.</div>
  </div>
</footer>

</body>
</html>
```